Business Card Re-Design/Update

We'd like to update out business cards. I've included our current "Style guide" which has the colour scheme of the organisation in it. I've also included the branding files with logos etc in them.

I've also included a copy of one of our existing cards so that you can see how ugly/dated they look. I'd like a fresh modern corporate look.

Target Market(s)

These are for our clients, potential clients, industry contacts - like all business cards

Contact Information for Business Card

Name
Position
Company Address - Level 1, 47 Fernby Street, Carlow Qld 4072
Direct Phone
mobile
Email
Website -www.korvalit.com.au
Logo

Colors

Designer to choose colors to be used in the design.

Requirements
Must have
• Main Logo
• Cards will need to be editable to be able to personalize them for each new employee.
Nice to have
• The MapOut, ShipWell, KeepSteady would be okay to have if they can be sensibly and professionally added to the look without detracting from the main imagery.
• Maybe they could go on the back of the card? will leave this to your creative discretion as to whether/where they fit.
Should not have
• Should not have decorative or script fonts

```html
<!DOCTYPE html>
<html lang="en">
<head>
<meta charset="utf-8">
<title>korvalIT business card</title>
<link rel="stylesheet" href="https://fonts.googleapis.com/css2?family=Roboto:wght@400;500;700&family=Roboto+Condensed:wght@500;700&display=swap">
<style>
  :root {
    --backdrop: #2b2b2c;
    --brand-red: #d3161d;
    --brand-red-deep: #b81117;
    --charcoal: #231f20;
    --paper: #f1f1f1;
    --ink: #2a2a2a;
    --white: #ffffff;
  }
  * { box-sizing: border-box; margin: 0; padding: 0; }
  html, body { width: 1200px; height: 960px; overflow: hidden; }
  body {
    background: var(--backdrop);
    font-family: "Roboto", Arial, sans-serif;
    position: relative;
  }
  .card {
    position: absolute;
    width: 600px;
    height: 342px;
    box-shadow: 0 2px 6px rgba(0,0,0,.45);
  }
  /* front */
  .card--front { left: 322px; top: 108px; background: var(--paper); display: flex; }
  .contact-panel { width: 268px; height: 100%; display: flex; flex-direction: column; background: var(--charcoal); }
  .identity {
    height: 88px;
    background: linear-gradient(180deg, var(--brand-red), var(--brand-red-deep));
    padding: 24px 0 0 27px;
    color: var(--white);
  }
  .identity__name { font-family: "Roboto Condensed", Arial, sans-serif; font-weight: 700; font-size: 21px; letter-spacing: .2px; }
  .identity__role { font-family: "Roboto Condensed", Arial, sans-serif; font-weight: 500; font-size: 15px; margin-top: 1px; }
  .divider { height: 2px; background: #e6e6e6; }
  .details { flex: 1; padding: 32px 0 0 28px; color: var(--white); font-size: 14px; line-height: 19px; }
  .details__address { margin-bottom: 8px; }
  .details__list { list-style: none; }
  .details__list li { display: flex; align-items: center; gap: 8px; }
  .details__list svg { width: 13px; height: 13px; fill: var(--white); flex: none; }
  .web-band {
    height: 50px;
    background: linear-gradient(180deg, var(--brand-red), var(--brand-red-deep));
    color: var(--white);
    font-size: 14px;
    letter-spacing: 1.2px;
    padding: 15px 0 0 28px;
  }
  .brand-side { flex: 1; display: flex; align-items: center; justify-content: center; gap: 12px; padding-bottom: 16px; }
  .brand-side__mark { width: 30px; height: 30px; background: var(--brand-red); }
  .brand-side__name { font-size: 34px; font-weight: 500; color: var(--ink); letter-spacing: -.3px; }
  /* back */
  .card--back { left: 320px; top: 493px; background: var(--charcoal); color: var(--white); }
  .back-brand { position: absolute; left: 0; right: 0; top: 95px; display: flex; justify-content: center; align-items: center; gap: 18px; }
  .back-brand__mark { width: 56px; height: 56px; background: var(--white); }
  .back-brand__name { font-size: 62px; font-weight: 500; letter-spacing: -.5px; }
  .services { position: absolute; left: 0; right: 0; top: 275px; display: flex; justify-content: center; gap: 36px; list-style: none; }
  .services li { display: flex; align-items: center; gap: 9px; font-size: 27px; font-weight: 500; letter-spacing: -.4px; }
  .services li::before { content: ""; width: 22px; height: 22px; background: var(--white); }
</style>
</head>
<body>
  <section class="card card--front" aria-label="Business card front">
    <div class="contact-panel">
      <header class="identity">
        <h1 class="identity__name">DANA WHITFIELD</h1>
        <p class="identity__role">Business Development Manager</p>
      </header>
      <div class="divider"></div>
      <div class="details">
        <p class="details__address">Level 1, 47 Fernby Street<br>Carlow Qld 4072</p>
        <ul class="details__list">
          <li><svg viewBox="0 0 16 16" aria-hidden="true"><path d="M3.6 1.2l2.3 2.6-1.2 1.9c.9 2 2.7 3.8 4.7 4.7l1.9-1.2 2.6 2.3-1.3 2.3C7.4 13.4 2.6 8.6 1.3 2.5z"/></svg>+61 (0)7 3900 1240</li>
          <li><svg viewBox="0 0 16 16" aria-hidden="true"><path d="M3.6 1.2l2.3 2.6-1.2 1.9c.9 2 2.7 3.8 4.7 4.7l1.9-1.2 2.6 2.3-1.3 2.3C7.4 13.4 2.6 8.6 1.3 2.5z"/></svg>+61 (0)7 3900 1257</li>
          <li><svg viewBox="0 0 16 16" aria-hidden="true"><path d="M4 0h8v16H4zM5.5 2v10h5V2z"/></svg>+61 (0)455 610 384</li>
          <li><svg viewBox="0 0 16 16" aria-hidden="true"><path d="M4 1h8v4H4zM1 6h14v6h-2v3H3v-3H1zm3 4v4h8v-4z"/></svg>+61 (0)7 3900 1299</li>
          <li><svg viewBox="0 0 16 16" aria-hidden="true"><path d="M1 3h14v10H1zm1.5 1.2L8 8.6l5.5-4.4z"/></svg>dwhitfield@korvalit.com.au</li>
        </ul>
      </div>
      <div class="divider"></div>
      <p class="web-band">www.korvalit.com.au</p>
    </div>
    <div class="brand-side">
      <span class="brand-side__mark" aria-hidden="true"></span>
      <span class="brand-side__name">korvalIT</span>
    </div>
  </section>

  <section class="card card--back" aria-label="Business card back">
    <div class="back-brand">
      <span class="back-brand__mark" aria-hidden="true"></span>
      <span class="back-brand__name">korvalIT</span>
    </div>
    <ul class="services">
      <li>MapOut</li>
      <li>ShipWell</li>
      <li>KeepSteady</li>
    </ul>
  </section>
</body>
</html>
```